Bookkeeping business needs a digital and print flyer

We need a flyer to promote our virtual bookkeeping services to small and mid-sized businesses in the United States. We want the content and design of the flyer to be consistent with our website: www.brightlanebookkeeping.example. We would like both a print version and a digital version of the flyer.

```html
<!DOCTYPE html>
<html lang="en">
<head>
<meta charset="utf-8">
<title>Bright Lane Bookkeeping – Virtual Bookkeeping Flyer</title>
<link href="https://fonts.googleapis.com/css2?family=Roboto:wght@400;500;700&display=swap" rel="stylesheet">
<style>
  :root{
    --ink:#111111;
    --text:#1f1f1f;
    --yellow:#f4c51c;
    --paper:#ffffff;
    --stage:#ececec;
    --rule:#9a9a9a;
    --photo-a:#efe7df;
    --photo-b:#c9b7a6;
  }
  *{box-sizing:border-box;margin:0;padding:0}
  html,body{width:1056px;height:1200px;overflow:hidden}
  body{background:var(--stage);font-family:'Roboto',Arial,sans-serif;color:var(--text)}
  .flyer{position:absolute;left:88px;top:31px;width:880px;height:1138px;background:var(--paper);box-shadow:0 6px 24px rgba(0,0,0,.18);overflow:hidden}
  .abs{position:absolute}

  .header-photo{left:360px;top:0;width:520px;height:310px;background:linear-gradient(90deg,rgba(255,255,255,1) 0%,rgba(239,231,223,.9) 22%,var(--photo-a) 45%,var(--photo-b) 100%)}
  .brand-name{left:28px;top:80px;font-family:'Roboto',Arial,sans-serif;font-weight:700;font-size:26px;line-height:32px;color:var(--ink)}
  .title{left:28px;top:157px;font-weight:700;font-size:34px;line-height:40px;color:var(--ink)}
  .title .accent{display:block;color:var(--yellow)}
  .tagline{left:28px;top:250px;font-size:15px;line-height:19px;color:var(--ink)}

  .intro-band{left:0;top:310px;width:880px;height:95px;background:var(--ink);color:#fff;padding:18px 28px 0;font-size:13px;line-height:20px}

  .col-head{font-weight:500;font-size:20px;line-height:26px;color:var(--yellow)}
  .col-sub{font-weight:700;font-size:13px;line-height:17px;color:var(--ink)}
  .icon{width:58px;height:58px}
  .check-list{list-style:none}
  .check-list li{position:relative;padding-left:31px;font-size:13px;line-height:16px;color:var(--text)}
  .check-list li svg{position:absolute;left:0;top:1px;width:13px;height:13px}

  .pain-icon{left:28px;top:428px}
  .pain-head{left:104px;top:430px;width:300px}
  .pain-list{left:28px;top:532px;width:370px}
  .pain-list li{margin-bottom:16px}
  .col-divider{left:414px;top:517px;width:1px;height:273px;background:var(--rule)}

  .gain-icon{left:470px;top:430px}
  .gain-head{left:551px;top:426px;width:300px}
  .gain-head .col-head{font-size:20px;line-height:27px}
  .gain-list{left:470px;top:560px;width:400px}
  .gain-list li{margin-bottom:17px;padding-left:41px}

  .accent-rule{left:28px;top:840px;width:828px;height:3px;background:var(--yellow)}
  .portrait{left:690px;top:770px;width:160px;height:282px;background:linear-gradient(180deg,#e9e6e2 0%,#5b6478 55%,#2b3350 100%);border-radius:80px 80px 0 0}
  .meet-tag{left:28px;top:843px;height:32px;width:170px;background:var(--yellow);clip-path:polygon(0 0,100% 0,84% 100%,0 100%);font-weight:700;font-size:22px;line-height:32px;padding-left:8px;color:var(--ink)}
  .bio{left:28px;width:610px;font-size:13px;line-height:16.5px;color:var(--text)}
  .bio-1{top:894px}
  .bio-2{top:980px}
  .footer-rule{left:28px;top:1054px;width:828px;height:2px;background:var(--ink)}

  .contact-row{left:28px;top:1068px;width:828px;display:flex;justify-content:space-between;align-items:center}
  .contact{display:flex;align-items:center;gap:12px;font-weight:700;font-size:15px;color:var(--ink)}
  .contact-badge{width:34px;height:34px;border-radius:50%;background:var(--ink);display:flex;align-items:center;justify-content:center}
  .contact-badge svg{width:20px;height:20px}
</style>
</head>
<body>
<main class="flyer">
  <div class="abs header-photo" role="img" aria-label="Photo of a tidy desk with laptop, smartphone, pen and notebook"></div>

  <div class="abs brand-name">Bright Lane Bookkeeping</div>

  <h1 class="abs title">Virtual Bookkeeping<span class="accent">for Small Business</span></h1>
  <p class="abs tagline">Build Your Business by Focusing on<br>What You Love</p>

  <section class="abs intro-band">
    Did you get into business because you loved recording finances?&nbsp; Reconciling bank statements?<br>
    Prepping for taxes? Of course not!&nbsp; Only nerdy bookkeepers enjoy these things.<br>
    You want to follow your passion, do what&nbsp; you do best to build a booming business.
  </section>

  <svg class="abs icon pain-icon" viewBox="0 0 58 58" fill="none" stroke="#111" stroke-width="1.6">
    <circle cx="16" cy="12" r="6"/><circle cx="42" cy="12" r="6"/><circle cx="29" cy="30" r="8"/>
    <path d="M6 30c0-6 4-10 10-10s10 4 10 10"/><path d="M32 30c0-6 4-10 10-10s10 4 10 10"/>
    <path d="M15 54c0-8 6-14 14-14s14 6 14 14"/>
  </svg>
  <div class="abs pain-head">
    <div class="col-head">Overwhelmed?</div>
    <div class="col-sub">Build your business by focusing on what you<br>love, not what drains the life out of you!</div>
  </div>
  <ul class="abs check-list pain-list">
    <li><svg viewBox="0 0 14 14" fill="none" stroke="#333" stroke-width="1.2"><circle cx="7" cy="7" r="6"/><path d="M4.2 7.2l2 2 3.6-4"/></svg>Do you feel pulled in so many directions you don't<br>know which way is up?</li>
    <li><svg viewBox="0 0 14 14" fill="none" stroke="#333" stroke-width="1.2"><circle cx="7" cy="7" r="6"/><path d="M4.2 7.2l2 2 3.6-4"/></svg>Do you hate that shoebox of receipts sitting on<br>your desk?</li>
    <li><svg viewBox="0 0 14 14" fill="none" stroke="#333" stroke-width="1.2"><circle cx="7" cy="7" r="6"/><path d="M4.2 7.2l2 2 3.6-4"/></svg>Do you wish you could just do the parts of your<br>business that you enjoy?</li>
    <li><svg viewBox="0 0 14 14" fill="none" stroke="#333" stroke-width="1.2"><circle cx="7" cy="7" r="6"/><path d="M4.2 7.2l2 2 3.6-4"/></svg>Do you dread logging into LedgerPro?</li>
    <li><svg viewBox="0 0 14 14" fill="none" stroke="#333" stroke-width="1.2"><circle cx="7" cy="7" r="6"/><path d="M4.2 7.2l2 2 3.6-4"/></svg>Do you panic at tax time?</li>
    <li><svg viewBox="0 0 14 14" fill="none" stroke="#333" stroke-width="1.2"><circle cx="7" cy="7" r="6"/><path d="M4.2 7.2l2 2 3.6-4"/></svg>Do you feel like you've lost control of<br>your finances?</li>
    <li><svg viewBox="0 0 14 14" fill="none" stroke="#333" stroke-width="1.2"><circle cx="7" cy="7" r="6"/><path d="M4.2 7.2l2 2 3.6-4"/></svg>Do you wish you could pay yourself more but<br>aren't sure if you can?</li>
  </ul>
  <div class="abs col-divider"></div>

  <svg class="abs icon gain-icon" viewBox="0 0 58 58" fill="none" stroke="#111" stroke-width="1.6">
    <path d="M29 12c-10 0-17 7-17 16 0 6 3 10 7 13v6h20v-6c4-3 7-7 7-13 0-9-7-16-17-16z"/>
    <path d="M21 51h16M23 55h12"/>
    <path d="M22 38v-6M28 38v-10M34 38v-14"/>
    <path d="M29 2v5M10 10l4 4M48 10l-4 4M4 28h5M49 28h5"/>
  </svg>
  <div class="abs gain-head">
    <div class="col-head">Take charge of your business<br>and concentrate on your<br>strengths to become its hero!</div>
    <div class="col-sub">Outsource your bookkeeping!</div>
  </div>
  <ul class="abs check-list gain-list">
    <li><svg viewBox="0 0 14 14" fill="none" stroke="#333" stroke-width="1.2"><circle cx="7" cy="7" r="6"/><path d="M4.2 7.2l2 2 3.6-4"/></svg>Take back your time</li>
    <li><svg viewBox="0 0 14 14" fill="none" stroke="#333" stroke-width="1.2"><circle cx="7" cy="7" r="6"/><path d="M4.2 7.2l2 2 3.6-4"/></svg>Do more of what you love</li>
    <li><svg viewBox="0 0 14 14" fill="none" stroke="#333" stroke-width="1.2"><circle cx="7" cy="7" r="6"/><path d="M4.2 7.2l2 2 3.6-4"/></svg>Focus on your strengths and what you do best</li>
    <li><svg viewBox="0 0 14 14" fill="none" stroke="#333" stroke-width="1.2"><circle cx="7" cy="7" r="6"/><path d="M4.2 7.2l2 2 3.6-4"/></svg>Confidently make business decisions</li>
    <li><svg viewBox="0 0 14 14" fill="none" stroke="#333" stroke-width="1.2"><circle cx="7" cy="7" r="6"/><path d="M4.2 7.2l2 2 3.6-4"/></svg>Sail through tax time</li>
    <li><svg viewBox="0 0 14 14" fill="none" stroke="#333" stroke-width="1.2"><circle cx="7" cy="7" r="6"/><path d="M4.2 7.2l2 2 3.6-4"/></svg>Save over the expense of a full-time employee</li>
    <li><svg viewBox="0 0 14 14" fill="none" stroke="#333" stroke-width="1.2"><circle cx="7" cy="7" r="6"/><path d="M4.2 7.2l2 2 3.6-4"/></svg>Pay yourself more</li>
    <li><svg viewBox="0 0 14 14" fill="none" stroke="#333" stroke-width="1.2"><circle cx="7" cy="7" r="6"/><path d="M4.2 7.2l2 2 3.6-4"/></svg>Experience financial peace</li>
  </ul>

  <div class="abs accent-rule"></div>
  <div class="abs portrait" role="img" aria-label="Portrait photo of the bookkeeper, Marissa, in a navy blouse"></div>
  <div class="abs meet-tag">Meet Marissa</div>
  <p class="abs bio bio-1">Hey there! I might be a bookkeeping nerd, but I still love to have some fun! You can catch me hanging out with my family, playing and teaching music, or cruising on my Marlowe trail bike. I'm also a pro at trip planning and love to hit up the mountains, lakes, and beaches for some R &amp; R time.</p>
  <p class="abs bio bio-2">Being a small business owner is tough and I can totally relate. Between bookkeeping and trying to balance business and personal life, it can get overwhelming. I'm all about supporting entrepreneurs and helping small business owners reach their goals. Let's take your business to the next level together!</p>
  <div class="abs footer-rule"></div>

  <div class="abs contact-row">
    <div class="contact">
      <span class="contact-badge"><svg viewBox="0 0 20 20" fill="none" stroke="#f4c51c" stroke-width="1.6"><path d="M5 3l3 3-2 2c1 2 3 4 5 5l2-2 3 3-2 3C8 17 3 12 2 5z"/></svg></span>
      555-014-2290
    </div>
    <div class="contact">
      <span class="contact-badge"><svg viewBox="0 0 20 20" fill="none" stroke="#f4c51c" stroke-width="1.6"><rect x="3" y="5" width="14" height="10"/><path d="M3 5l7 6 7-6"/></svg></span>
      marissa@brightlanebookkeeping.example
    </div>
    <div class="contact">
      <span class="contact-badge"><svg viewBox="0 0 20 20" fill="none" stroke="#f4c51c" stroke-width="1.4"><circle cx="10" cy="10" r="7"/><ellipse cx="10" cy="10" rx="3" ry="7"/><path d="M3 10h14M4.5 6h11M4.5 14h11"/></svg></span>
      www.brightlanebookkeeping.example
    </div>
  </div>
</main>
</body>
</html>
```